I need a simple infographic that describes the 4 basic elements of how to effectively create change.

The overall title (Gentle Pressure Relentlessly Applied) should be at the top of the infographic. Subtitle is: "Leading Change".
There are four steps:
1. Alignment- Agreement on Approach
2. Transparency- Metrics for Assurance
3. Skills- Training and Coaching
4. Integrity- Culture of Accountability

Target Market(s)

Business Leaders in a training workshop

Font styles to use
Serif

Requirements
Must have
• Here are the 4 elements of the Infographic: Please show them in order.
• 1. Agreement on Approach. (Alignment)
• 2. Metrics for Assurance (Transparency)
• 3. Training and Coaching (Skills)
• 4. Culture of Accountability (Integrity)
Nice to have
• Cool Graphics that depict the 4 steps.
Should not have
• Pictures.

```html
<!DOCTYPE html>
<html lang="en">
<head>
<meta charset="utf-8">
<title>Gentle Pressure Relentlessly Applied – Leading Change</title>
<link href="https://fonts.googleapis.com/css2?family=Montserrat:wght@300;400;800&display=swap" rel="stylesheet">
<style>
  :root {
    --page-bg: #f1efec;
    --poster-blue: #00a8e1;
    --white: #ffffff;
    --shadow: rgba(0, 40, 70, 0.28);
  }
  * { margin: 0; padding: 0; box-sizing: border-box; }
  html, body {
    width: 1200px; height: 1200px; overflow: hidden;
    background: var(--page-bg);
    font-family: "Montserrat", Arial, sans-serif;
  }
  .poster {
    position: absolute; left: 131px; top: 0;
    width: 938px; height: 1200px;
    background: var(--poster-blue);
    color: var(--white);
  }
  .poster-frame {
    position: absolute; left: 43px; top: 43px; right: 43px; bottom: 48px;
    border: 1.5px solid rgba(255,255,255,0.85);
  }
  .brand {
    position: absolute; left: 0; right: 0; top: 80px;
    display: flex; justify-content: center; align-items: center; gap: 14px;
  }
  .brand-dot {
    width: 64px; height: 64px; border-radius: 50%;
    border: 3px solid var(--white);
  }
  .brand-name {
    font-weight: 300; font-size: 33px; letter-spacing: -0.5px;
  }
  .title {
    position: absolute; left: 0; right: 0; top: 160px;
    text-align: center; font-weight: 800; font-size: 56px;
    line-height: 51px; letter-spacing: 1px;
  }
  .title-rule {
    position: absolute; left: 314px; width: 310px; top: 276px;
    border-top: 1.5px solid var(--white);
  }
  .subtitle {
    position: absolute; left: 0; right: 0; top: 288px;
    text-align: center; font-weight: 300; font-size: 27px; letter-spacing: 1.5px;
  }
  .chain { position: absolute; left: 0; top: 0; }
  .step { position: absolute; transform: translateY(-50%); white-space: nowrap; }
  .step--left { right: calc(938px - 399px); text-align: right; }
  .step--right { left: 498px; text-align: left; }
  .step-name { font-weight: 800; font-size: 30px; letter-spacing: 1.5px; line-height: 34px; }
  .step-desc { font-weight: 300; font-size: 20.5px; letter-spacing: 0.8px; line-height: 28px; }
</style>
</head>
<body>
<main class="poster">
  <div class="poster-frame"></div>

  <header class="brand">
    <span class="brand-dot"></span>
    <span class="brand-name">THE HARLOW GROUP</span>
  </header>

  <h1 class="title">GENTLE PRESSURE<br>RELENTLESSLY APPLIED</h1>
  <div class="title-rule"></div>
  <p class="subtitle">LEADING CHANGE</p>

  <svg class="chain" width="938" height="1200" viewBox="0 0 938 1200">
    <defs>
      <filter id="soft-shadow" x="-20%" y="-20%" width="140%" height="140%">
        <feDropShadow dx="0" dy="4" stdDeviation="6" flood-color="#00284a" flood-opacity="0.3"/>
      </filter>
    </defs>
    <g class="chain-body" filter="url(#soft-shadow)" fill="#ffffff" stroke="#ffffff">
      <polyline points="492,471 411,650 492,831 411,1017" fill="none" stroke-width="52" stroke-linejoin="round"/>
      <circle cx="492" cy="471" r="76"/>
      <circle cx="411" cy="650" r="76"/>
      <circle cx="492" cy="831" r="76"/>
      <circle cx="411" cy="1017" r="76"/>
    </g>

    <!-- alignment: list icon -->
    <g class="badge badge--alignment">
      <circle cx="492" cy="471" r="60" fill="#00a8e1" stroke="#eef4f7" stroke-width="4"/>
      <g fill="#ffffff">
        <rect x="460" y="444" width="64" height="9"/>
        <rect x="460" y="458" width="64" height="9"/>
        <rect x="460" y="472" width="64" height="9"/>
        <rect x="460" y="486" width="64" height="9"/>
      </g>
    </g>

    <!-- transparency: chart and magnifier -->
    <g class="badge badge--transparency">
      <circle cx="411" cy="650" r="60" fill="#00a8e1" stroke="#eef4f7" stroke-width="4"/>
      <g fill="none" stroke="#ffffff" stroke-width="3">
        <rect x="381" y="622" width="44" height="58"/>
        <rect x="387" y="660" width="7" height="16"/>
        <rect x="398" y="652" width="7" height="24"/>
        <rect x="409" y="664" width="7" height="12"/>
        <circle cx="423" cy="640" r="15" fill="#00a8e1"/>
        <line x1="434" y1="651" x2="446" y2="663" stroke-width="5"/>
      </g>
    </g>

    <!-- skills: illustration area -->
    <g class="badge badge--skills">
      <circle cx="492" cy="831" r="60" fill="#00a8e1" stroke="#eef4f7" stroke-width="4"/>
      <circle cx="492" cy="831" r="36" fill="#33b9e7" role="img" aria-label="Icon of a person fitting puzzle pieces together"/>
    </g>

    <!-- integrity: pie chart -->
    <g class="badge badge--integrity">
      <circle cx="411" cy="1017" r="60" fill="#00a8e1" stroke="#eef4f7" stroke-width="4"/>
      <path d="M411,1017 L411,977 A40,40 0 1 1 371,1017 Z" fill="#ffffff" transform="translate(-4,-4)"/>
      <path d="M416,1022 L456,1022 A40,40 0 0 1 416,1062 Z" fill="none" stroke="#ffffff" stroke-width="3"/>
    </g>
  </svg>

  <section class="step step--left" style="top:466px">
    <h2 class="step-name">ALIGNMENT</h2>
    <p class="step-desc">AGREEMENT ON APPROACH</p>
  </section>
  <section class="step step--right" style="top:646px">
    <h2 class="step-name">TRANSPARENCY</h2>
    <p class="step-desc">METRICS FOR ASSURANCE</p>
  </section>
  <section class="step step--left" style="top:835px">
    <h2 class="step-name">SKILLS</h2>
    <p class="step-desc">TRAINING AND COACHING</p>
  </section>
  <section class="step step--right" style="top:1015px">
    <h2 class="step-name">INTEGRITY</h2>
    <p class="step-desc">CULTURE OF ACCOUNTABILITY</p>
  </section>
</main>
</body>
</html>
```